Business Card Design

Business sales of reconditioned / used batteries with mobile delivery and install services. Customers base majority are auto car sales lots and individuals.

Card need to convey quality product reliability and quick prompt professional service.

Card must reflect excellence in customer care and product being offered

Target Market(s)

Auto car lots new and used. Auto repair shops. Individuals.

Industry/Entity Type

Business

Contact Information for Business Card

Batteries Q-Swift
Cars, Trucks, Boats, Motorcycles, lawn mowers, power tools
Delivery & install available most vehicles
Mon-Sat 9-6pm
Dale Morrick 501-738-2054
*product warranty 6 month shelf life battery/1 year blems battery

```html
<!DOCTYPE html>
<html lang="en">
<head>
<meta charset="utf-8">
<title>Batteries Q-Swift – Business Card</title>
<link rel="stylesheet" href="https://fonts.googleapis.com/css2?family=Source+Sans+3:wght@400;700&display=swap">
<style>
  :root {
    --page: #ffffff;
    --card: #ffffff;
    --band: #000000;
    --red: #e30613;
    --ink: #111111;
    --text: #1a1a1a;
    --white: #ffffff;
  }
  html, body {
    margin: 0;
    width: 1200px;
    height: 1000px;
    overflow: hidden;
    background: var(--page);
    font-family: "Source Sans 3", "Myriad Pro", Arial, sans-serif;
  }
  .card {
    position: absolute;
    left: 60px;
    top: 185px;
    width: 1086px;
    height: 638px;
    background: var(--card);
    box-shadow: 0 2px 10px rgba(0,0,0,0.35);
    overflow: hidden;
  }
  .card__band {
    position: absolute;
    left: 0; top: 0;
    width: 100%;
    height: 198px;
    background: var(--band);
  }
  .card__stripe {
    position: absolute;
    left: 0; top: 198px;
    width: 100%;
    height: 25px;
    background: linear-gradient(90deg, rgba(227,6,19,0) 12%, rgba(236,110,80,0.7) 45%, var(--red) 88%);
  }
  .brand {
    position: absolute;
    left: 0; right: 0;
    top: 62px;
    display: flex;
    justify-content: center;
    align-items: center;
    gap: 22px;
  }
  .brand__mark {
    width: 30px;
    height: 30px;
    background: var(--red);
  }
  .brand__name {
    margin: 0;
    color: var(--white);
    font-weight: 700;
    font-size: 68px;
    line-height: 1;
    letter-spacing: 0.5px;
  }
  .services {
    position: absolute;
    left: 60px;
    top: 232px;
    margin: 0;
    padding: 0;
    list-style: none;
  }
  .services__item {
    display: flex;
    align-items: center;
    height: 39.5px;
    font-size: 31px;
    color: var(--text);
  }
  .services__icon {
    width: 28px;
    height: 22px;
    margin-right: 10px;
    flex: none;
  }
  .warranty {
    position: absolute;
    left: 57px;
    top: 560px;
    margin: 0;
    font-size: 24.5px;
    color: var(--text);
  }
  .contact {
    position: absolute;
    right: 61px;
    top: 296px;
    text-align: right;
  }
  .contact__name {
    margin: 0;
    color: var(--red);
    font-size: 42px;
    line-height: 48px;
    font-weight: 400;
  }
  .contact__phone {
    margin: 0;
    color: var(--ink);
    font-size: 57px;
    line-height: 60px;
    font-weight: 700;
  }
  .contact__hours {
    margin: 34px 0 0;
    color: var(--text);
    font-size: 35px;
    line-height: 40px;
  }
</style>
</head>
<body>
  <div class="card">
    <div class="card__band"></div>
    <div class="card__stripe"></div>

    <div class="brand">
      <h1 class="brand__name">BATTERIES Q-SWIFT</h1>
      <span class="brand__mark"></span>
    </div>

    <ul class="services">
      <li class="services__item"><svg class="services__icon" viewBox="0 0 28 22"><path d="M0 0h7l7 11-7 11H0l7-11z M12 0h7l7 11-7 11h-7l7-11z" fill="#e30613"/></svg>Cars</li>
      <li class="services__item"><svg class="services__icon" viewBox="0 0 28 22"><path d="M0 0h7l7 11-7 11H0l7-11z M12 0h7l7 11-7 11h-7l7-11z" fill="#e30613"/></svg>Trucks</li>
      <li class="services__item"><svg class="services__icon" viewBox="0 0 28 22"><path d="M0 0h7l7 11-7 11H0l7-11z M12 0h7l7 11-7 11h-7l7-11z" fill="#e30613"/></svg>Boats</li>
      <li class="services__item"><svg class="services__icon" viewBox="0 0 28 22"><path d="M0 0h7l7 11-7 11H0l7-11z M12 0h7l7 11-7 11h-7l7-11z" fill="#e30613"/></svg>Motorcycles</li>
      <li class="services__item"><svg class="services__icon" viewBox="0 0 28 22"><path d="M0 0h7l7 11-7 11H0l7-11z M12 0h7l7 11-7 11h-7l7-11z" fill="#e30613"/></svg>Lawn mowers</li>
      <li class="services__item"><svg class="services__icon" viewBox="0 0 28 22"><path d="M0 0h7l7 11-7 11H0l7-11z M12 0h7l7 11-7 11h-7l7-11z" fill="#e30613"/></svg>Power tools</li>
      <li class="services__item"><svg class="services__icon" viewBox="0 0 28 22"><path d="M0 0h7l7 11-7 11H0l7-11z M12 0h7l7 11-7 11h-7l7-11z" fill="#e30613"/></svg>Delivery &amp; Install available</li>
      <li class="services__item"><svg class="services__icon" viewBox="0 0 28 22"><path d="M0 0h7l7 11-7 11H0l7-11z M12 0h7l7 11-7 11h-7l7-11z" fill="#e30613"/></svg>Most vehicles</li>
    </ul>

    <p class="warranty">*product warranty 6 month shelf life battery/1 year blems battery</p>

    <div class="contact">
      <p class="contact__name">DALE MORRICK</p>
      <p class="contact__phone">501-738-2054</p>
      <p class="contact__hours">Monday-Saturday 9-6pm</p>
    </div>
  </div>
</body>
</html>
```